Casa Verdal business card
Indoor Environmental Specialists
Professional
Rick Olvany-Trel
President
5172 North Quarrel Ave Unit 248
Palmcrest Shores FL, 33519
rick@casaverdalcrew.com
www.casaverdalcrew.com
CMI MRSR381 CMRC MRSA219
Serving:
Southeast Florida and the Caribbean
Indoor Mold Screen Assessments.
Indoor Air Quality Testing.
Mold Remediation Contractor.
Moisture Intrusion Surveys.
Thermal Imaging Inspection.
UV Air Sanitizer Sales & Service.
Casa Verdal Logo
Casa Verdal Logo On The Left Side

```html
<!DOCTYPE html>
<html lang="en">
<head>
<meta charset="utf-8">
<title>Casa Verdal Stationery</title>
<link rel="stylesheet" href="https://fonts.googleapis.com/css2?family=Open+Sans:wght@400;600;700&display=swap">
<style>
:root{
  --bg:#d9d4cc;
  --paper:#ffffff;
  --navy:#0d3f8f;
  --blue:#1f6fc7;
  --sky:#5ca8e6;
  --green:#5fae2e;
  --lime:#9bcf3a;
  --ink:#3a4656;
  --muted:#8a96a4;
}
*{margin:0;padding:0;box-sizing:border-box}
html,body{width:1200px;height:439px;overflow:hidden}
body{background:var(--bg);font-family:"Open Sans",sans-serif;color:var(--ink);position:relative}
.piece{position:absolute;background:var(--paper);box-shadow:0 2px 6px rgba(0,0,0,.25);overflow:hidden}
.wave{position:absolute;left:0;bottom:0;width:100%}
.brand{display:flex;align-items:center;gap:4px;font-weight:700;color:var(--navy);letter-spacing:.3px;white-space:nowrap}
.brand .dot{border-radius:50%;background:var(--green);flex:none}
.tag{font-size:4px;color:var(--green);font-weight:600;white-space:nowrap}
.contact{white-space:nowrap}

/* business cards */
.card{left:19px;width:168px;height:96px}
.card-front{top:67px}
.card-front .brand{position:absolute;left:10px;top:34px;font-size:8px}
.card-front .brand .dot{width:9px;height:9px}
.card-front .tag{position:absolute;left:10px;top:47px}
.card-front .person{position:absolute;left:90px;top:9px;font-size:4px;line-height:1.45;white-space:nowrap}
.card-front .person b{font-size:5.5px;color:var(--navy)}
.card-back{top:180px;height:103px}
.card-back ul{position:absolute;left:10px;top:9px;list-style:none;font-size:4.6px;line-height:1.55}
.card-back li::before{content:"";display:inline-block;width:3px;height:3px;border-radius:50%;background:var(--green);margin-right:4px;vertical-align:middle}
.card-back .serving{position:absolute;left:10px;top:64px;font-size:4.4px;color:var(--navy);font-weight:600}
.card-back .mark{position:absolute;right:12px;top:26px;width:34px;height:34px;border-radius:50%;background:var(--green)}
.card-dark{top:293px;height:103px;background:linear-gradient(160deg,var(--blue),var(--navy))}
.card-dark .brand{position:absolute;left:36px;top:44px;font-size:11px;color:#fff}
.card-dark .brand .dot{width:12px;height:12px;background:var(--lime)}

/* letterheads */
.letter{top:24px;width:264px;height:372px}
.letter-main{left:204px}
.letter-next{left:499px}
.letter .brand{position:absolute;left:18px;top:22px;font-size:10px}
.letter .brand .dot{width:12px;height:12px}
.letter .contact{position:absolute;right:16px;top:14px;font-size:4.4px;line-height:1.5;color:var(--muted);text-align:right}
.faint{position:absolute;left:72px;top:116px;width:120px;height:120px;border-radius:50%;border:2px solid rgba(31,111,199,.12);display:flex;align-items:center;justify-content:center;font-weight:700;font-size:12px;color:rgba(31,111,199,.14)}
.letter-next .brand{left:88px;top:26px}

/* envelopes */
.env{left:797px;width:391px}
.env-green{top:12px;height:120px;background:linear-gradient(180deg,var(--lime),var(--green))}
.env-blue{top:96px;height:144px}
.env-white{top:230px;height:100px}
.env-addr{top:324px;height:103px}
.flap{position:absolute;left:0;top:0;width:100%}
.env-green .dot-c,.env-blue .dot-c{position:absolute;left:187px;width:16px;height:16px;border-radius:50%;background:var(--green);border:2px solid #fff}
.env-green .dot-c{top:68px}
.env-blue .dot-c{top:68px}
.env-addr .brand{position:absolute;left:10px;top:12px;font-size:8px}
.env-addr .brand .dot{width:9px;height:9px}
.env-addr .contact{position:absolute;left:10px;top:26px;font-size:4.4px;line-height:1.5;color:var(--muted)}
</style>
</head>
<body>

<section class="piece card card-front">
  <div class="brand"><span class="dot"></span>CASA VERDAL</div>
  <div class="tag">Indoor Environmental Specialists</div>
  <div class="person"><b>Rick Olvany-Trel</b><br>President<br>5172 North Quarrel Ave Unit 248<br>Palmcrest Shores FL, 33519<br>rick@casaverdalcrew.com<br>www.casaverdalcrew.com<br>CMI MRSR381 CMRC MRSA219</div>
  <svg class="wave" viewBox="0 0 168 16" height="16" preserveAspectRatio="none"><path d="M0 8 C50 0 110 14 168 4 V16 H0Z" fill="var(--green)"/><path d="M0 11 C55 4 110 16 168 8 V16 H0Z" fill="var(--navy)"/></svg>
</section>

<section class="piece card card-back">
  <ul>
    <li>Indoor Mold Screen Assessments.</li>
    <li>Indoor Air Quality Testing.</li>
    <li>Mold Remediation Contractor.</li>
    <li>Moisture Intrusion Surveys.</li>
    <li>Thermal Imaging Inspection.</li>
    <li>UV Air Sanitizer Sales &amp; Service.</li>
  </ul>
  <div class="serving">Serving: Southeast Florida and the Caribbean</div>
  <div class="mark"></div>
  <svg class="wave" viewBox="0 0 168 16" height="16" preserveAspectRatio="none"><path d="M0 8 C50 0 110 14 168 4 V16 H0Z" fill="var(--green)"/><path d="M0 11 C55 4 110 16 168 8 V16 H0Z" fill="var(--navy)"/></svg>
</section>

<section class="piece card card-dark">
  <div class="brand"><span class="dot"></span>CASA VERDAL</div>
</section>

<section class="piece letter letter-main">
  <div class="brand"><span class="dot"></span>CASA VERDAL</div>
  <div class="contact">5172 North Quarrel Ave Unit 248<br>Palmcrest Shores FL, 33519<br>rick@casaverdalcrew.com<br>www.casaverdalcrew.com</div>
  <div class="faint">CASA VERDAL</div>
  <svg class="wave" viewBox="0 0 264 24" height="24" preserveAspectRatio="none"><path d="M0 10 C80 0 170 20 264 6 V24 H0Z" fill="var(--green)"/><path d="M0 15 C90 6 170 24 264 12 V24 H0Z" fill="var(--navy)"/></svg>
</section>

<section class="piece letter letter-next">
  <div class="brand"><span class="dot"></span>CASA VERDAL</div>
  <div class="faint">CASA VERDAL</div>
  <svg class="wave" viewBox="0 0 264 24" height="24" preserveAspectRatio="none"><path d="M0 10 C80 0 170 20 264 6 V24 H0Z" fill="var(--green)"/><path d="M0 15 C90 6 170 24 264 12 V24 H0Z" fill="var(--navy)"/></svg>
</section>

<section class="piece env env-green">
  <svg class="flap" viewBox="0 0 391 120" height="120" preserveAspectRatio="none"><path d="M0 0 H391 L200 80 Z" fill="#fff" opacity=".25"/></svg>
  <div class="dot-c"></div>
</section>

<section class="piece env env-blue">
  <svg class="flap" viewBox="0 0 391 144" height="144" preserveAspectRatio="none"><path d="M0 0 H391 L200 84 Z" fill="var(--blue)"/><path d="M0 0 H391 L200 70 Z" fill="var(--sky)"/></svg>
  <div class="dot-c"></div>
</section>

<section class="piece env env-white">
  <svg class="flap" viewBox="0 0 391 100" height="100" preserveAspectRatio="none"><path d="M0 0 L200 60 L391 0" fill="none" stroke="#d5dbe2" stroke-width="1.5"/></svg>
</section>

<section class="piece env env-addr">
  <div class="brand"><span class="dot"></span>CASA VERDAL</div>
  <div class="contact">5172 North Quarrel Ave Unit 248<br>Palmcrest Shores FL, 33519</div>
  <svg class="wave" viewBox="0 0 391 18" height="18" preserveAspectRatio="none"><path d="M0 8 C120 0 260 16 391 4 V18 H0Z" fill="var(--green)"/><path d="M0 12 C130 4 260 18 391 9 V18 H0Z" fill="var(--navy)"/></svg>
</section>

</body>
</html>
```